I would like a single page website for Skyward Rentals Pacific. In the file list provided there is basic information to be included as well as our logo with colors, fonts and images to be included.
Site must be very simple and be able to be loaded onto smart phones etc very quickly.
Site needs to be very smart in appearance

Target Market(s)

All prospective drone customers from Police to Parties.

Industry/Entity Type

Hire

Requirements
Must have
• Must have variation of color schemes supplied
Nice to have
• Must be very eye catching without going over the top
Should not have
• Anything slow to load.

```html
<!DOCTYPE html>
<html lang="en">
<head>
<meta charset="utf-8">
<title>Skyward Rentals Pacific</title>
<link rel="stylesheet" href="https://fonts.googleapis.com/css2?family=Oswald:wght@300;400;500&family=Open+Sans:wght@400;600&display=swap">
<style>
:root{
  --green:#8dc63f;
  --green-dark:#5f9c1e;
  --ink:#2b2b2b;
  --text:#555;
  --muted:#777;
  --paper:#ffffff;
  --grey-band:#f1f1f1;
  --footer:#232323;
  --footer-line:#3a3a3a;
  --sky-top:#6aa6dc;
  --sky-bottom:#e9eef2;
  --grass:#5d9a2c;
}
*{box-sizing:border-box;margin:0;padding:0}
html,body{width:1200px;height:2539px;overflow:hidden}
body{position:relative;background:var(--paper);font-family:"Open Sans",Arial,sans-serif;color:var(--text)}
.abs{position:absolute}

/* header */
.site-header{left:0;top:0;width:1200px;height:108px;background:var(--paper);border-bottom:1px solid #e4e4e4;z-index:3}
.brand{left:100px;top:30px;display:flex;align-items:center;gap:12px}
.brand-dot{width:26px;height:26px;border-radius:50%;background:var(--green)}
.brand-name{font-family:"Oswald",sans-serif;font-weight:500;font-size:27px;color:var(--green-dark);line-height:1;letter-spacing:.5px}
.main-nav{right:100px;top:42px;display:flex}
.main-nav a{font-family:"Oswald",sans-serif;font-weight:300;font-size:16px;color:var(--ink);text-decoration:none;padding:0 26px;border-left:1px solid #e2e2e2;line-height:24px}
.main-nav a:first-child{border-left:none}

/* hero */
.hero{left:0;top:108px;width:1200px;height:603px;background:linear-gradient(170deg,var(--sky-top) 0%,#c9dceb 35%,var(--sky-bottom) 60%,#cfe0c8 70%,var(--grass) 100%)}
.hero-title{right:97px;top:202px;text-align:right;font-family:"Oswald",sans-serif;line-height:1.2}
.hero-title .l1{display:block;font-size:44px;color:var(--ink);font-weight:400}
.hero-title .l2{display:block;font-size:52px;color:var(--green-dark);font-weight:400}
.hero-arrow{top:385px;width:34px;height:34px;border-radius:50%;background:#333;display:flex;align-items:center;justify-content:center}

/* service cards */
.service{top:640px;width:315px;height:202px;background:var(--green);box-shadow:0 6px 8px rgba(0,0,0,.18);text-align:center;color:#fff;padding-top:88px}
.service-icon{position:absolute;left:50%;top:-56px;margin-left:-63px;width:126px;height:126px;border-radius:50%;background:#222;border:5px solid var(--green);display:flex;align-items:center;justify-content:center}
.service h3{font-family:"Oswald",sans-serif;font-weight:400;font-size:20px;margin-bottom:10px}
.service p{font-size:10.5px;line-height:20px;padding:0 20px}

/* welcome */
.welcome-band{left:0;top:711px;width:1200px;height:347px;background:var(--grey-band)}
.welcome-title{left:0;top:885px;width:1200px;text-align:center;font-family:"Oswald",sans-serif;font-size:32px;color:var(--ink);font-weight:400}
.welcome-title span{color:var(--green-dark)}
.welcome-text{left:170px;top:945px;width:860px;text-align:center;font-size:11px;line-height:21px;color:var(--muted)}

/* drone points */
.points-title{left:98px;top:1104px;font-family:"Oswald",sans-serif;font-weight:300;font-size:32px;color:var(--ink)}
.points-intro{left:98px;top:1157px;width:540px;font-size:12px;line-height:21px;color:var(--muted)}
.points-list{left:98px;top:1218px;list-style:none}
.points-list li{display:flex;align-items:center;gap:12px;font-size:13px;color:#444;height:28.4px}
.tablet{left:670px;top:1138px;width:430px;height:322px;border-radius:22px;background:#111;border:3px solid #d6d6d6;box-shadow:0 6px 10px rgba(0,0,0,.15)}
.tablet-screen{position:absolute;left:38px;top:30px;width:348px;height:256px;background:linear-gradient(180deg,#b6c8b5 0%,#9bb88a 50%,#6d9b3f 100%)}

/* why */
.why-band{left:0;top:1532px;width:1200px;height:496px;background:var(--grey-band)}
.why-title{left:98px;top:1566px;font-family:"Oswald",sans-serif;font-weight:500;font-size:33px;color:var(--green-dark)}
.why-sub{left:98px;top:1614px;font-family:"Oswald",sans-serif;font-weight:300;font-size:20px;color:var(--ink)}
.why-card{top:1674px;width:316px}
.why-photo{width:316px;height:196px;border:4px solid #fff;box-shadow:0 1px 3px rgba(0,0,0,.15)}
.why-card h3{font-family:"Open Sans",sans-serif;font-weight:400;font-size:20px;color:#333;margin:17px 0 8px}
.why-card p{font-size:11px;line-height:20px;color:var(--muted)}

/* news */
.news-title{left:98px;top:2082px;font-family:"Oswald",sans-serif;font-weight:300;font-size:20px;color:var(--ink)}
.news-item{top:2133px;display:flex;gap:27px}
.news-photo{width:186px;height:164px}
.news-body{width:280px}
.news-body h4{font-family:"Open Sans",sans-serif;font-weight:400;font-size:15px;color:#333;margin-top:-2px}
.news-date{font-family:"Oswald",sans-serif;font-size:13px;color:var(--green-dark);margin:18px 0 8px}
.news-body p{font-size:11px;line-height:20px;color:var(--muted)}
.news-more{display:block;font-size:12px;color:#333;margin-top:8px}

/* footer */
.site-footer{left:0;top:2362px;width:1200px;height:177px;background:var(--footer)}
.cta{left:98px;top:2390px;font-family:"Oswald",sans-serif;font-weight:300;font-size:20px;color:#fff}
.cta-phone{left:98px;top:2428px;font-size:15px;color:var(--green)}
.address{left:497px;top:2396px;font-size:14px;line-height:29px;color:#ddd}
.social{left:906px;top:2394px;display:flex;gap:9px}
.social span{width:34px;height:34px;border-radius:50%;background:#3c3c3c;display:block}
.footer-rule{left:98px;top:2470px;width:1004px;height:1px;background:var(--footer-line)}
.copyright{left:0;top:2494px;width:1200px;text-align:center;font-size:11px;color:#aaa}
</style>
</head>
<body>

<header class="site-header abs">
  <div class="brand abs"><span class="brand-dot"></span><span class="brand-name">Skyward Rentals Pacific</span></div>
  <nav class="main-nav abs">
    <a href="#">Home</a><a href="#">About Us</a><a href="#">Our Services</a><a href="#">Special</a><a href="#">Contact Us</a>
  </nav>
</header>

<section class="hero abs" role="img" aria-label="Two operators flying a white camera drone over a grassy hillside under a cloudy blue sky"></section>
<h1 class="hero-title abs"><span class="l1">Drone Aerial Photography</span><span class="l2">&amp; video services</span></h1>
<div class="hero-arrow abs" style="left:37px"><svg width="12" height="14" viewBox="0 0 12 14"><path d="M8 2 3 7l5 5" stroke="#fff" stroke-width="2.4" fill="none"/></svg></div>
<div class="hero-arrow abs" style="left:1125px"><svg width="12" height="14" viewBox="0 0 12 14"><path d="M4 2l5 5-5 5" stroke="#fff" stroke-width="2.4" fill="none"/></svg></div>

<div class="welcome-band abs"></div>

<article class="service abs" style="left:101px">
  <div class="service-icon"><svg width="56" height="56" viewBox="0 0 56 56" fill="#fff"><rect x="12" y="22" width="32" height="26"/><polygon points="8,24 28,8 48,24"/><rect x="24" y="34" width="8" height="14" fill="#222"/></svg></div>
  <h3>Drone Parties</h3>
  <p>Lorem ipsum dolor sit amet, consectetuer adipiscing elit. Aenean commodo ligula eget dolor. Aenean massa. Lorem ipsum dolor sit amet, consectetuer</p>
</article>
<article class="service abs" style="left:444px">
  <div class="service-icon"><svg width="60" height="56" viewBox="0 0 60 56" fill="#fff"><rect x="8" y="14" width="36" height="18" rx="3" transform="rotate(15 26 23)"/><rect x="30" y="34" width="6" height="14"/><rect x="24" y="46" width="22" height="5"/></svg></div>
  <h3>Surveillance</h3>
  <p>Lorem ipsum dolor sit amet, consectetuer adipiscing elit. Aenean commodo ligula eget dolor. Aenean massa. Lorem ipsum dolor sit amet, consectetuer</p>
</article>
<article class="service abs" style="left:786px">
  <div class="service-icon"><svg width="50" height="56" viewBox="0 0 50 56"><path d="M14 26V17a11 11 0 0 1 22 0" stroke="#fff" stroke-width="5" fill="none"/><rect x="8" y="26" width="34" height="26" rx="3" fill="#fff"/><rect x="23" y="34" width="4" height="10" fill="#222"/></svg></div>
  <h3>Security</h3>
  <p>Lorem ipsum dolor sit amet, consectetuer adipiscing elit. Aenean commodo ligula eget dolor. Aenean massa. Lorem ipsum dolor sit amet, consectetuer</p>
</article>

<h2 class="welcome-title abs">Welcome To <span>Skyward Rentals Pacific</span></h2>
<p class="welcome-text abs">Lorem ipsum dolor sit amet, consectetur adipiscing elit, sed do eiusmod tempor incididunt ut labore et dolore magna aliqua. Ut enim ad minim veniam, quis nostrud exercitation ullamco laboris nisi ut aliquip ex ea commodo consequat. Duis aute irure dolor in reprehenderit in voluptate velit esse cillum dolore eu fugiat nulla pariatur. Excepteur sint occaecat cupidatat non proident, sunt in culpa qui officia deserunt mollit anim id est laborum</p>

<h2 class="points-title abs">Drones Points</h2>
<p class="points-intro abs">Sed ut perspiciatis unde omnis iste natus error sit voluptatem accusantium doloremque laudantium, totam rem aperiam, eaque ipsa quae ab illo inventore</p>
<ul class="points-list abs">
  <li><svg width="12" height="10" viewBox="0 0 12 10"><path d="M1 5l3.5 3.5L11 1" stroke="#5f9c1e" stroke-width="2" fill="none"/></svg>Special Occasions, Children's Birthday Parties, Weddings</li>
  <li><svg width="12" height="10" viewBox="0 0 12 10"><path d="M1 5l3.5 3.5L11 1" stroke="#5f9c1e" stroke-width="2" fill="none"/></svg>Sporting events –4K&nbsp; Video of yourself participating in marathons etc</li>
  <li><svg width="12" height="10" viewBox="0 0 12 10"><path d="M1 5l3.5 3.5L11 1" stroke="#5f9c1e" stroke-width="2" fill="none"/></svg>Real Estate Brochures</li>
  <li><svg width="12" height="10" viewBox="0 0 12 10"><path d="M1 5l3.5 3.5L11 1" stroke="#5f9c1e" stroke-width="2" fill="none"/></svg>Construction project updates for remote stake holders</li>
  <li><svg width="12" height="10" viewBox="0 0 12 10"><path d="M1 5l3.5 3.5L11 1" stroke="#5f9c1e" stroke-width="2" fill="none"/></svg>Surveillance – Police, Local councils worksafe etc</li>
  <li><svg width="12" height="10" viewBox="0 0 12 10"><path d="M1 5l3.5 3.5L11 1" stroke="#5f9c1e" stroke-width="2" fill="none"/></svg>Building/Roof Condition Inspections</li>
  <li><svg width="12" height="10" viewBox="0 0 12 10"><path d="M1 5l3.5 3.5L11 1" stroke="#5f9c1e" stroke-width="2" fill="none"/></svg>Lost pets</li>
  <li><svg width="12" height="10" viewBox="0 0 12 10"><path d="M1 5l3.5 3.5L11 1" stroke="#5f9c1e" stroke-width="2" fill="none"/></svg>Accident reconstructions</li>
  <li><svg width="12" height="10" viewBox="0 0 12 10"><path d="M1 5l3.5 3.5L11 1" stroke="#5f9c1e" stroke-width="2" fill="none"/></svg>Insurance assessing</li>
</ul>
<div class="tablet abs"><div class="tablet-screen" role="img" aria-label="White camera drone hovering above a suburban lawn"></div></div>

<section class="why-band abs"></section>
<h2 class="why-title abs">WHY PEOPLE CHOOSE US?</h2>
<p class="why-sub abs">Donec sodales sagittis magna sed consequat leo eget bibendum sodales</p>
<article class="why-card abs" style="left:99px">
  <div class="why-photo" role="img" aria-label="Snowboarder jumping against a bright blue sky" style="background:linear-gradient(160deg,#3f7fc8,#9cc4ea 60%,#eef3f8)"></div>
  <h3>Sporting Events</h3>
  <p>Sed ut perspiciatis unde omnis iste natus error sit volupta-tem accusantium doloremque laudantium, totam rem aperiam, eaque ipsa quae ab...</p>
</article>
<article class="why-card abs" style="left:442px">
  <div class="why-photo" role="img" aria-label="Construction worker in hard hat reviewing plans at a building site" style="background:linear-gradient(160deg,#7aa6d6,#c7a77a 60%,#6a4d3a)"></div>
  <h3>Construction Project</h3>
  <p>Sed ut perspiciatis unde omnis iste natus error sit volupta-tem accusantium doloremque laudantium, totam rem aperiam, eaque ipsa quae ab...</p>
</article>
<article class="why-card abs" style="left:785px">
  <div class="why-photo" role="img" aria-label="Suburban house with front lawn and path" style="background:linear-gradient(180deg,#8cbbe6,#a9b3a8 50%,#5e9a34)"></div>
  <h3>Real Estate Brochures</h3>
  <p>Sed ut perspiciatis unde omnis iste natus error sit volupta-tem accusantium doloremque laudantium, totam rem aperiam, eaque ipsa quae ab...</p>
</article>

<h2 class="news-title abs">LATEST NEWS</h2>
<article class="news-item abs" style="left:98px">
  <div class="news-photo" role="img" aria-label="Multirotor drone flying near a rooftop" style="background:linear-gradient(180deg,#8fb9e0,#b59a7a 60%,#6b8f3a)"></div>
  <div class="news-body">
    <h4>Nulla at diam ornare, aliquam urna</h4>
    <div class="news-date">APRIL 25, 2015</div>
    <p>Nulla at diam ornare, aliquam urna vel, commodo urna. Nam id risus a est luctus consectetur quis eget libero. Suspendisse potenti. Pellentesque habitant morbi tristique senectus</p>
    <a class="news-more" href="#">Read More +</a>
  </div>
</article>
<article class="news-item abs" style="left:630px">
  <div class="news-photo" role="img" aria-label="Large drone flying above operators in a park" style="background:linear-gradient(180deg,#cfdbe6,#a7c08d 60%,#4f7f2a)"></div>
  <div class="news-body">
    <h4>Nulla at diam ornare, aliquam urna</h4>
    <div class="news-date">APRIL 25, 2015</div>
    <p>Nulla at diam ornare, aliquam urna vel, commodo urna. Nam id risus a est luctus consectetur quis eget libero. Suspendisse potenti. Pellentesque habitant morbi tristique senectus</p>
    <a class="news-more" href="#">Read More +</a>
  </div>
</article>

<footer class="site-footer abs"></footer>
<p class="cta abs">For a Free Consultation Call :</p>
<p class="cta-phone abs">0400 555 019</p>
<address class="address abs" style="font-style:normal">12 Harbour View Place,<br>Brightwater, NS 45 20.</address>
<div class="social abs"><span></span><span></span><span></span><span></span><span></span></div>
<div class="footer-rule abs"></div>
<p class="copyright abs">© 2015 Skyward Rentals Pacific - All Rights Reserved</p>

</body>
</html>
```